Penfield Draft Works (PDWorks.net)

We need a Wordpress-based site designed for a client who provides writing and editing services for the IT industry. We have a wireframe complete for the homepage, but need all internal pages designed (based on homepage wireframe) and the entire site coded for WP.

Internal pages include: "Our Work" (with samples & testimonials); "Capabilities" (with sections to address "strategy", "coaching", "writing" and "editing"); "About Us"; and a Contact page.

Will provide all copywriting, writing samples, testimonials, and client logos.

We completely realize/acknowledge the subject matter is visually BORING! Anything at all that can be done to make it look visually appealing would be *great*! Stock photography is fine.

Please feel free to ask any questions whatsoever. Thanks for your time!

```html
<!DOCTYPE html>
<html lang="en">
<head>
<meta charset="utf-8">
<title>Penfield Draft Works</title>
<link href="https://fonts.googleapis.com/css2?family=Lato:wght@400;700;900&family=Oswald:wght@500&display=swap" rel="stylesheet">
<style>
:root{
  --orange:#f97a0e;
  --blue:#1565c8;
  --link:#1a6fc9;
  --ink:#333333;
  --body:#4a4a4a;
  --dark:#1b1b1b;
  --tile:#f2f2f2;
}
*{margin:0;padding:0;box-sizing:border-box}
html,body{width:1200px;height:3508px;overflow:hidden}
body{position:relative;background:#fff;font-family:'Lato',sans-serif;color:var(--body)}
.abs{position:absolute}
.brand{font-family:'Oswald',sans-serif;font-weight:500;font-size:28px;line-height:34px;color:#111;text-transform:uppercase;letter-spacing:.3px}
.nav{left:341px;top:50px;display:flex;gap:43px;font-size:14.5px;font-weight:700;color:#111;text-transform:uppercase}
.nav .active{color:var(--link)}
.btn{display:flex;align-items:center;justify-content:center;background:var(--orange);color:#fff;font-weight:700;font-size:14.5px;text-transform:uppercase;border-radius:30px;letter-spacing:.2px}
.shapes{left:0;top:0;width:1200px;height:3508px}
.hero-title{left:0;top:400px;width:1200px;text-align:center;color:#fff;font-weight:900;font-size:51px;line-height:60px;text-transform:uppercase}
.lead{left:0;top:955px;width:1200px;text-align:center;color:var(--ink);font-weight:700;font-size:38px;line-height:46px}
.photo{border-radius:42px 14px 42px 14px}
.card-title{text-align:center;color:var(--link);font-weight:700;font-size:24px}
.card-text{text-align:center;font-size:16.5px;line-height:26px;color:var(--body)}
.sec-title{left:0;width:1200px;text-align:center;font-size:37px;font-weight:700}
.client{background:var(--tile);height:84px;width:241px;display:flex;align-items:center;justify-content:center;gap:10px;font-size:30px;font-weight:700;color:#333}
.client i{display:block;width:26px;height:26px;border-radius:50%;background:var(--orange)}
.work-title{width:328px;text-align:center;color:var(--link);font-weight:700;font-size:23.5px;line-height:32px}
.work-text{width:328px;text-align:center;font-size:16.5px;line-height:26px}
.cta{text-align:center;color:var(--ink);font-weight:700;font-size:24px;line-height:36px}
.email{left:703px;top:2960px;width:339px;height:54px;border:1px solid #b9c2cc;border-radius:30px;background:#fff;padding-left:20px;display:flex;align-items:center;font-size:12.5px;color:#333;text-transform:uppercase}
.foot{color:#e6e6e6}
.foot-h{color:var(--orange);font-weight:700;font-size:26px}
.foot-list{list-style:none;font-size:16.5px;line-height:36px;color:#eee}
.social{left:75px;top:3380px;display:flex;gap:22px}
.social span{width:22px;height:22px;border-radius:50%;background:#fff;display:block}
</style>
</head>
<body>

<svg class="abs shapes" viewBox="0 0 1200 3508" aria-hidden="false">
  <defs>
    <linearGradient id="heroTone" x1="0" y1="0" x2="1" y2="1">
      <stop offset="0" stop-color="#8a6a5a"/>
      <stop offset=".35" stop-color="#b0532c"/>
      <stop offset=".7" stop-color="#6e5448"/>
      <stop offset="1" stop-color="#a8948a"/>
    </linearGradient>
    <linearGradient id="clientTone" x1="0" y1="0" x2="1" y2="0">
      <stop offset="0" stop-color="#1e1e20"/>
      <stop offset=".5" stop-color="#3a3838"/>
      <stop offset="1" stop-color="#242426"/>
    </linearGradient>
    <linearGradient id="contactTone" x1="0" y1="0" x2="1" y2="0">
      <stop offset="0" stop-color="#c9d6e0"/>
      <stop offset=".5" stop-color="#eef2f5"/>
      <stop offset="1" stop-color="#dfe9ef"/>
    </linearGradient>
  </defs>
  <polygon role="img" aria-label="Photo of a man writing in a notebook beside a laptop" fill="url(#heroTone)" points="0,114 1200,114 1200,817 0,906"/>
  <polygon fill="var(--blue)" points="599,868 1200,824 1200,913"/>

  <polygon fill="var(--blue)" points="0,1570 599,1614 0,1659"/>
  <polygon role="img" aria-label="Photo of a business meeting with a handshake" fill="url(#clientTone)" points="0,1659 1200,1580 1200,1957 0,2043"/>
  <polygon fill="var(--blue)" points="599,2006 1200,1957 1200,2052"/>

  <polygon fill="var(--blue)" points="0,2704 599,2744 0,2792"/>
  <polygon role="img" aria-label="Soft photo of a hand writing in a spiral notebook" fill="url(#contactTone)" points="0,2792 1200,2710 1200,3080 0,3175"/>
  <polygon fill="var(--blue)" points="600,3118 1200,3070 1200,3140"/>
  <polygon fill="var(--dark)" points="0,3180 1200,3130 1200,3508 0,3508"/>

  <line x1="633" y1="2819" x2="568" y2="3064" stroke="#333" stroke-width="1.2"/>
</svg>

<header>
  <div class="abs brand" style="left:77px;top:24px">Penfield Draft<br>Works</div>
  <nav class="abs nav">
    <span class="active">Home</span><span>Our Work</span><span>Capabilities</span><span>About Us</span><span>Contact Us</span>
  </nav>
  <div class="abs btn" style="left:942px;top:33px;width:184px;height:54px">Get In Touch</div>
</header>

<h1 class="abs hero-title">Communicate your expertise and<br>your customer successes</h1>

<section>
  <h2 class="abs lead">Text copy that explains in concise, snappy terms the<br>value you provide to customers.</h2>

  <div class="abs photo" role="img" aria-label="Strategy sketch illustration" style="left:75px;top:1084px;width:241px;height:203px;background:linear-gradient(135deg,#f4f4f4,#c9d3de)"></div>
  <div class="abs photo" role="img" aria-label="Photo of two women working together" style="left:346px;top:1084px;width:241px;height:203px;background:linear-gradient(135deg,#d8d2cc,#6b5a4e)"></div>
  <div class="abs photo" role="img" aria-label="Photo of a hand writing on paper" style="left:616px;top:1084px;width:241px;height:203px;background:linear-gradient(135deg,#8a6e5c,#e9e6e4)"></div>
  <div class="abs photo" role="img" aria-label="Photo of a document being edited with a red pen" style="left:885px;top:1084px;width:241px;height:203px;background:linear-gradient(135deg,#b8b6b2,#eceae6)"></div>

  <div class="abs card-title" style="left:75px;top:1316px;width:241px">Strategy</div>
  <div class="abs card-title" style="left:346px;top:1316px;width:241px">Coaching</div>
  <div class="abs card-title" style="left:616px;top:1316px;width:241px">Writing</div>
  <div class="abs card-title" style="left:885px;top:1316px;width:241px">Editing</div>

  <p class="abs card-text" style="left:75px;top:1353px;width:241px">Sed ut perspiciatis unde omnis iste natus error sit voluptatem accusantium.</p>
  <p class="abs card-text" style="left:346px;top:1353px;width:241px">Sed ut perspiciatis unde omnis iste natus error sit voluptatem accusantium.</p>
  <p class="abs card-text" style="left:616px;top:1353px;width:241px">Sed ut perspiciatis unde omnis iste natus error sit voluptatem accusantium.</p>
  <p class="abs card-text" style="left:885px;top:1353px;width:241px">Sed ut perspiciatis unde omnis iste natus error sit voluptatem accusantium.</p>

  <div class="abs btn" style="left:478px;top:1475px;width:244px;height:53px">View Our Capabilities</div>
</section>

<section>
  <h2 class="abs sec-title" style="top:1716px;color:#fff">Our Past &amp; Current Clients</h2>
  <div class="abs client" style="left:75px;top:1796px"><i></i>Keelstone</div>
  <div class="abs client" style="left:346px;top:1796px"><i style="background:var(--blue)"></i>Brindle</div>
  <div class="abs client" style="left:616px;top:1796px">Harrow &amp; Co</div>
  <div class="abs client" style="left:885px;top:1796px"><i></i>Veltrix</div>
</section>

<section>
  <h2 class="abs sec-title" style="top:2087px;color:var(--ink)">Our Work Done</h2>

  <div class="abs photo" role="img" aria-label="Photo of hands typing on a laptop" style="left:75px;top:2166px;width:328px;height:231px;background:linear-gradient(135deg,#7a6a5e,#d9cfc6)"></div>
  <div class="abs photo" role="img" aria-label="Photo of a man writing notes at a laptop" style="left:437px;top:2166px;width:328px;height:231px;background:linear-gradient(135deg,#6f93b8,#d8dfe6)"></div>
  <div class="abs photo" role="img" aria-label="Photo of a hand writing in a notebook" style="left:799px;top:2166px;width:328px;height:231px;background:linear-gradient(135deg,#b5761f,#6a4a28)"></div>

  <div class="abs work-title" style="left:75px;top:2413px">How Align Your Applications to the Optimal Infrastructure Envirorrrnent</div>
  <div class="abs work-title" style="left:437px;top:2413px">How Align Your Applications to the Optimal Infrastructure Envirorrrnent</div>
  <div class="abs work-title" style="left:799px;top:2413px">How Align Your Applications to the Optimal Infrastructure Envirorrrnent</div>

  <p class="abs work-text" style="left:75px;top:2515px">Sed ut perspiciatis unde omnis iste natus error sit voluptatem accusantium.</p>
  <p class="abs work-text" style="left:437px;top:2515px">Sed ut perspiciatis unde omnis iste natus error sit voluptatem accusantium.</p>
  <p class="abs work-text" style="left:799px;top:2515px">Sed ut perspiciatis unde omnis iste natus error sit voluptatem accusantium.</p>

  <div class="abs btn" style="left:478px;top:2612px;width:244px;height:55px">View Our Work</div>
</section>

<section>
  <p class="abs cta" style="left:60px;top:2867px;width:540px">Feel free to contact us with any questions<br>We're happy to help.</p>
  <div class="abs btn" style="left:242px;top:2960px;width:176px;height:54px">Get In Touch</div>
  <p class="abs cta" style="left:632px;top:2867px;width:480px">Editorial inspiration delivered<br>straight to your inbox.</p>
  <div class="abs email">Enter Email Address</div>
</section>

<footer class="foot">
  <div class="abs brand" style="left:77px;top:3236px;color:#fff">Penfield Draft<br>Works</div>
  <p class="abs" style="left:75px;top:3314px;font-size:14px;line-height:27px;color:#ddd">© Copyright 2021 PDWorks.net.<br><span style="font-size:13px">All Right Reserved</span></p>
  <div class="abs social" aria-label="Social media links"><span></span><span></span><span></span><span></span><span></span></div>

  <div class="abs foot-h" style="left:377px;top:3228px">Site Map</div>
  <ul class="abs foot-list" style="left:377px;top:3266px"><li>Home</li><li>Our Work</li><li>Capabilities</li><li>About Us</li><li>Contact Us</li></ul>

  <div class="abs foot-h" style="left:640px;top:3228px">Services</div>
  <ul class="abs foot-list" style="left:640px;top:3266px"><li>Strategy</li><li>Coaching</li><li>Writing</li><li>Editing</li></ul>

  <div class="abs foot-h" style="left:885px;top:3228px">Contact Info</div>
  <p class="abs" style="left:885px;top:3272px;font-size:16.5px;line-height:27.5px;color:#eee">220 Larkspur Row<br># 12, Maple Falls,<br>OR 97031</p>
  <div class="abs" style="left:885px;top:3362px;font-size:16.5px;color:#eee;display:flex;align-items:center;gap:16px">
    <svg width="16" height="16" viewBox="0 0 24 24"><path fill="#fff" d="M6.6 10.8a15 15 0 0 0 6.6 6.6l2.2-2.2a1 1 0 0 1 1-.25 11.4 11.4 0 0 0 3.6.57 1 1 0 0 1 1 1V20a1 1 0 0 1-1 1A17 17 0 0 1 3 4a1 1 0 0 1 1-1h3.5a1 1 0 0 1 1 1c0 1.25.2 2.45.57 3.57a1 1 0 0 1-.25 1z"/></svg>
    (555) 014-2290</div>
  <div class="abs" style="left:885px;top:3396px;font-size:16.5px;color:#eee;display:flex;align-items:center;gap:16px">
    <svg width="16" height="13" viewBox="0 0 24 18"><rect width="24" height="18" rx="2" fill="#fff"/><path d="M1 2l11 8 11-8" stroke="#1b1b1b" stroke-width="2" fill="none"/></svg>
    info@pdworks.net</div>
</footer>

</body>
</html>
```